The Radiant Scroll of Petitions, Mighty Petitions Across Every Season of Trial

I want a book cover design, The book is a prayer book. Pleas no design with only words. I want something creative and original. Something that attracts attention just by looking at the cover. Something powerful. This book is for people that are experiencing issues and need prayer. This book is also for those that want to pray and pray effectively. Not only will there be prayers. But they will learn the dynamics of prayer and how to pray effectively and from the right position. This book is filled with power yet effective prayers that will.have the ability to break bondages off people lives.
Below is some book covers that I found. I posted them to give an idea of what im looking for. Something that catches the attention of a reader.

Target Market(s)

Everyone, religious people

Industry/Entity Type

Religious

Font styles to use
Serif
Sans Serif

Requirements
Must have
• Creativity, originality,
Nice to have
• Professional looking. Powerful looking
Should not have
• Should not have just one color with big ole words across the whole book.

```html
<!DOCTYPE html>
<html lang="en">
<head>
<meta charset="utf-8">
<title>The Radiant Scroll of Petitions — Book Cover</title>
<link rel="stylesheet" href="https://fonts.googleapis.com/css2?family=Cormorant+Garamond:wght@600&family=Great+Vibes&display=swap">
<style>
  :root {
    --page-bg: #d8d5c9;
    --sky-night: #243468;
    --sky-teal: #2f6f8f;
    --sky-amber: #f0a848;
    --sky-gold: #f7de6a;
    --land-green: #5f7a3a;
    --river-silver: #e9ebe6;
    --river-shade: #bfc2bc;
    --title-red: #8a1414;
    --title-blue: #2b2e9c;
  }
  html, body {
    margin: 0;
    width: 927px;
    height: 1200px;
    overflow: hidden;
    background: var(--page-bg);
  }
  .cover {
    position: absolute;
    left: 73px;
    top: 18px;
    width: 780px;
    height: 1164px;
    overflow: hidden;
    box-shadow: 0 6px 18px rgba(0,0,0,.18);
  }
  .cover-art {
    position: absolute;
    inset: 0;
    background:
      radial-gradient(ellipse 22% 15% at 50% 25%, rgba(255,255,250,.98) 0%, rgba(255,255,240,.7) 45%, rgba(255,255,240,0) 100%),
      radial-gradient(ellipse 45% 30% at 50% 78%, rgba(255,255,255,.85) 0%, rgba(255,255,255,0) 100%),
      linear-gradient(180deg,
        var(--sky-night) 0%,
        #2a4a7e 18%,
        var(--sky-teal) 30%,
        #d9a25a 44%,
        var(--sky-amber) 52%,
        var(--sky-gold) 60%,
        var(--land-green) 63%,
        #7f8d4a 66%,
        var(--river-silver) 70%,
        #f4f4f0 86%,
        var(--river-shade) 100%);
  }
  .cover-title {
    position: absolute;
    left: 0;
    right: 0;
    top: 796px;
    margin: 0;
    text-align: center;
    font-weight: 400;
  }
  .title-lead {
    display: block;
    padding-left: 90px;
    font-family: "Cormorant Garamond", Georgia, serif;
    font-weight: 600;
    font-size: 30px;
    line-height: 1;
    letter-spacing: 0.2em;
    color: var(--title-red);
  }
  .title-main {
    display: block;
    margin-top: 22px;
    font-family: "Great Vibes", cursive;
    font-size: 132px;
    line-height: 1.05;
    color: var(--title-blue);
  }
</style>
</head>
<body>
  <main class="cover">
    <div class="cover-art" role="img" aria-label="Glowing heart of light with sparkles shining over a sunset sky, cliffs and a wide silver river"></div>
    <h1 class="cover-title">
      <span class="title-lead">The Radiant Scroll of</span>
      <span class="title-main">Petitions</span>
    </h1>
  </main>
</body>
</html>
```